Executive recruiting firm in need of business card design

Executive recruiting firm looking for a sleek, classy and modern business card design; card itself will be square shape, rounded edges and soft touch paper, our colors are dark blues in the navy color scale, silvers and grays. Reference our website for a better idea of our company's feel and goals at Tarvex-Up.com - our company message is "Employee Engagement Begins at Recruitment" this should be on the card

```html
<!DOCTYPE html>
<html lang="en">
<head>
<meta charset="utf-8">
<title>Tarvex Up – Business Card</title>
<link rel="stylesheet" href="https://fonts.googleapis.com/css2?family=Open+Sans:wght@300;400;600;700&display=swap">
<style>
  :root {
    --navy: #161a4a;
    --navy-text: #1b1f55;
    --silver-light: #e4e5e8;
    --ink: #2b2b2b;
    --paper: #ffffff;
    --backdrop: #e9e9ec;
  }
  * { margin: 0; padding: 0; box-sizing: border-box; }
  html, body {
    width: 1200px; height: 900px; overflow: hidden;
    background: var(--backdrop);
    font-family: "Open Sans", Arial, sans-serif;
  }
  .stage { position: relative; width: 1200px; height: 900px; }
  .card {
    position: absolute; width: 400px; height: 400px;
    border-radius: 22px;
    box-shadow: 0 6px 18px rgba(0,0,0,0.18);
  }
  .card--front { left: 150px; top: 110px; background: var(--navy); }
  .card--back  { left: 650px; top: 390px; background: var(--paper); }

  .wordmark {
    position: absolute; font-weight: 300; font-size: 40px;
    letter-spacing: 5px; line-height: 1; white-space: nowrap;
  }
  .card--front .wordmark {
    left: 0; right: 0; top: 150px; text-align: center; color: var(--silver-light);
  }
  .card--back .wordmark { left: 36px; top: 44px; color: var(--navy-text); }

  .slogan {
    position: absolute; left: 40px; right: 40px; bottom: 48px; text-align: center;
    color: var(--silver-light); font-size: 14px; font-weight: 600; line-height: 1.5;
    letter-spacing: 0.5px; text-transform: uppercase;
  }

  .address {
    position: absolute; right: 32px; top: 130px; text-align: right;
    font-style: normal; font-size: 13px; line-height: 1.45; color: var(--ink);
  }

  .contact-person { position: absolute; left: 36px; top: 215px; color: var(--ink); }
  .contact-person__name {
    color: var(--navy-text); font-weight: 700; font-size: 19px; text-transform: uppercase;
  }
  .contact-person__role { font-size: 15px; margin-bottom: 10px; }
  .contact-list { list-style: none; font-size: 15px; }
  .contact-list li { display: flex; align-items: center; gap: 10px; height: 24px; }
  .contact-list svg { width: 12px; height: 12px; fill: var(--navy-text); flex: none; }
</style>
</head>
<body>
<main class="stage">
  <section class="card card--front" aria-label="Card front">
    <p class="wordmark">TARVEX UP</p>
    <p class="slogan">Employee Engagement Begins at Recruitment</p>
  </section>

  <section class="card card--back" aria-label="Card back">
    <p class="wordmark">TARVEX UP</p>

    <address class="address">1234, Address GoesHere,<br>Country name, 12345</address>

    <div class="contact-person">
      <p class="contact-person__name">Marcus Ellery</p>
      <p class="contact-person__role">Managing Director</p>
      <ul class="contact-list">
        <li>
          <svg viewBox="0 0 12 12" aria-hidden="true"><path d="M2.3 0.6 4 2.6 3.2 4.2c.7 1.6 2 2.9 3.6 3.6L8.4 7l2 1.7-.9 2c-4.8-.3-8.4-3.9-8.7-8.7z"/></svg>
          <span>(044)987650312</span>
        </li>
        <li>
          <svg viewBox="0 0 12 12" aria-hidden="true"><path d="M0.5 2.5h11v7h-11z M1.2 3 6 6.6 10.8 3" stroke="#fff" stroke-width="0.8"/></svg>
          <span>info@tarvex-up.com</span>
        </li>
        <li>
          <svg viewBox="0 0 12 12" aria-hidden="true"><circle cx="6" cy="6" r="5.5"/><path d="M0.8 6h10.4M6 0.6c-2.4 3-2.4 7.8 0 10.8M6 0.6c2.4 3 2.4 7.8 0 10.8" stroke="#fff" stroke-width="0.7" fill="none"/></svg>
          <span>www.Tarvex-Up.com</span>
        </li>
      </ul>
    </div>
  </section>
</main>
</body>
</html>
```